New Company Business Card design

Looking for a corporate looking business card utilising my new logo design - the logo i would like embossed as one option and flat as another - simplistic but stylish - less is more - we are an import export business launching into the market - i would like a couple of options as main background - Grey or Black

```html
<!DOCTYPE html>
<html lang="en">
<head>
<meta charset="utf-8">
<title>Meridian Trade Partners – Business Card</title>
<link rel="stylesheet" href="https://fonts.googleapis.com/css2?family=Cinzel:wght@500&family=Arimo:wght@400&display=swap">
<style>
  :root {
    --stage: #262628;
    --card-dark: #141415;
    --card-light: #efeff0;
    --brand-blue: #1f6fc2;
    --brand-grey: #8c8c8e;
    --rule: #a9a9ab;
    --ink: #1e1e1e;
  }
  * { margin: 0; padding: 0; box-sizing: border-box; }
  html, body { width: 1200px; height: 900px; overflow: hidden; }
  body {
    background: var(--stage);
    display: flex;
    flex-direction: column;
    align-items: center;
    justify-content: center;
    gap: 40px;
  }
  .card {
    width: 600px;
    height: 345px;
    border-radius: 22px;
    position: relative;
    overflow: hidden;
  }

  /* Back */
  .card--back {
    background: var(--card-dark);
    display: flex;
    flex-direction: column;
    align-items: center;
    justify-content: center;
  }
  .brand { display: flex; align-items: center; gap: 14px; }
  .brand__dot {
    width: 22px; height: 22px; border-radius: 50%;
    background: var(--brand-blue);
  }
  .brand__name {
    font-family: "Cinzel", serif;
    font-weight: 500;
    color: var(--brand-blue);
    font-size: 30px;
    letter-spacing: 1px;
    line-height: 1;
  }
  .tagline {
    font-family: "Cinzel", serif;
    color: var(--brand-grey);
    font-size: 11.5px;
    letter-spacing: 3.2px;
    text-transform: uppercase;
    border-top: 1px solid var(--rule);
    padding-top: 6px;
    margin-top: 10px;
  }
  .website {
    font-family: "Cinzel", serif;
    color: var(--brand-blue);
    font-size: 14px;
    letter-spacing: 1.5px;
    margin-top: 26px;
  }

  /* Front */
  .card--front {
    background: var(--card-light);
    color: var(--ink);
    padding: 44px 40px 36px;
  }
  .front__brand .brand__name { font-size: 26px; }
  .front__brand .tagline { font-size: 10px; letter-spacing: 3px; display: inline-block; }
  .front__divider {
    position: absolute; left: 40px; right: 40px; top: 150px;
    border-top: 1px solid var(--rule);
  }
  .person { position: absolute; left: 40px; top: 180px; }
  .person__name {
    font-family: "Cinzel", serif;
    color: var(--brand-blue);
    font-size: 21px;
    letter-spacing: 0.5px;
  }
  .person__role {
    font-family: "Arimo", sans-serif;
    font-size: 15px;
    margin-top: 2px;
  }
  .address {
    position: absolute; right: 40px; top: 184px;
    font-family: "Arimo", sans-serif;
    font-size: 15px;
    line-height: 1.35;
    text-align: right;
  }
  .contacts {
    position: absolute; left: 40px; bottom: 30px;
    list-style: none;
    border-top: 1px solid var(--rule);
    padding-top: 10px;
    width: 230px;
    font-family: "Arimo", sans-serif;
    font-size: 15px;
  }
  .contacts li { display: flex; align-items: center; gap: 9px; line-height: 1.4; }
  .contacts svg { width: 13px; height: 13px; fill: var(--brand-blue); flex: none; }
</style>
</head>
<body>
  <section class="card card--back" aria-label="Card back">
    <div class="brand">
      <span class="brand__dot"></span>
      <span class="brand__name">MERIDIAN TRADE PARTNERS</span>
    </div>
    <p class="tagline">Worldwide supply for every market</p>
    <p class="website">WWW.MERIDIANTRADE.COM</p>
  </section>

  <section class="card card--front" aria-label="Card front">
    <div class="front__brand">
      <p class="brand__name">MERIDIAN TRADE PARTNERS</p>
      <p class="tagline">Worldwide supply for every market</p>
    </div>
    <div class="front__divider"></div>

    <div class="person">
      <p class="person__name">DANIEL HARTLEY</p>
      <p class="person__role">Managing Director</p>
    </div>

    <p class="address">48 Harbour Road<br>Southport, 204518</p>

    <ul class="contacts">
      <li>
        <svg viewBox="0 0 16 16" aria-hidden="true"><path d="M2 5c0-2 2-3 6-3s6 1 6 3v1h-3V5H5v1H2zM4 7h8l2 7H2z"/></svg>
        044-987 654 321
      </li>
      <li>
        <svg viewBox="0 0 16 16" aria-hidden="true"><path d="M4 1h8v14H4zM5.5 3v9h5V3z"/></svg>
        044-987 654 321
      </li>
      <li>
        <svg viewBox="0 0 16 16" aria-hidden="true"><path d="M1 3h14v10H1zM2.5 4.5 8 9l5.5-4.5z"/></svg>
        info@meridiantrade.com
      </li>
    </ul>
  </section>
</body>
</html>
```